Local fast-growing company in the service sector

We are looking for a modern business card design, which should also appear on our letterheads

Target Market(s)

Private and industrial sectors

Contact Information for Business Card

Vorname Name
Kellberger Str. 18
73614 Lindenau
Tel.: 07146-839214-0
Name@agentur-kvtl.de

Colors
9d9d9d
919191
aaaaaa

Requirements
Must have
• The logo (file) in silver

```html
<!DOCTYPE html>
<html lang="de">
<head>
<meta charset="utf-8">
<title>KVTL Visitenkarte</title>
<link rel="stylesheet" href="https://fonts.googleapis.com/css2?family=PT+Sans:wght@400;700&display=swap">
<style>
  :root {
    --backdrop: #2b2b2b;
    --card: #0d0d0d;
    --card-edge: #1c1c1c;
    --divider: #1f1f1f;
    --silver: #aaaaaa;
    --silver-mid: #9d9d9d;
    --silver-dark: #919191;
    --text-light: #e4e4e4;
  }
  * { margin: 0; padding: 0; box-sizing: border-box; }
  html, body {
    width: 1200px; height: 900px; overflow: hidden;
    background: var(--backdrop);
    font-family: "PT Sans", Arial, sans-serif;
  }
  .stage {
    position: relative; width: 1200px; height: 900px;
    display: flex; align-items: center; justify-content: center; gap: 60px;
  }
  .card {
    position: relative; width: 510px; height: 312px;
    background: var(--card);
    border: 1px solid var(--card-edge);
    border-radius: 22px;
    overflow: hidden;
  }
  /* Contact side */
  .card--contact { display: flex; }
  .brand-block {
    width: 54%; display: flex; align-items: center; justify-content: center; gap: 14px;
  }
  .brand-mark {
    width: 26px; height: 26px; background: var(--silver);
  }
  .brand-name {
    font-weight: 700; font-size: 54px; letter-spacing: 2px; color: var(--silver);
  }
  .contact-block {
    width: 46%; border-left: 1px solid var(--divider);
    padding: 78px 0 0 26px; color: var(--text-light);
  }
  .contact-name {
    font-weight: 700; font-size: 17px; letter-spacing: 0.5px; margin-bottom: 14px;
  }
  .contact-address { font-size: 14px; line-height: 1.35; margin-bottom: 12px; }
  .contact-list { list-style: none; font-size: 14px; line-height: 1.35; }
  .contact-list li { display: flex; align-items: center; gap: 8px; }
  .contact-icon { width: 11px; height: 11px; fill: var(--silver); flex: none; }
  /* Logo side */
  .card--logo { display: flex; align-items: center; justify-content: center; gap: 18px; }
  .card--logo .brand-mark { width: 34px; height: 34px; }
  .card--logo .brand-name { font-size: 68px; }
</style>
</head>
<body>
<main class="stage">
  <section class="card card--contact">
    <div class="brand-block">
      <span class="brand-mark"></span>
      <span class="brand-name">KVTL</span>
    </div>
    <div class="contact-block">
      <p class="contact-name">VORNAME NAME</p>
      <p class="contact-address">Kellberger Str. 18<br>73614 Lindenau</p>
      <ul class="contact-list">
        <li>
          <svg class="contact-icon" viewBox="0 0 12 12" aria-hidden="true"><path d="M2.5 0.5 L4.5 0.5 L5.3 3 L4 4.2 Q5.2 6.8 7.8 8 L9 6.7 L11.5 7.5 L11.5 9.5 Q11.5 11.5 9.5 11.5 Q1 11 0.5 2.5 Q0.5 0.5 2.5 0.5Z"/></svg>
          07146-839214-0
        </li>
        <li>
          <svg class="contact-icon" viewBox="0 0 12 12" aria-hidden="true"><path d="M0 2 H12 V10 H0 Z M0.8 2.6 L6 6.8 L11.2 2.6 V3.6 L6 7.8 L0.8 3.6Z" fill-rule="evenodd"/></svg>
          Name@agentur-kvtl.de
        </li>
        <li>
          <svg class="contact-icon" viewBox="0 0 12 12" aria-hidden="true"><circle cx="6" cy="6" r="5.5"/><path d="M0.5 6 H11.5 M6 0.5 V11.5 M3 1.5 Q1 6 3 10.5 M9 1.5 Q11 6 9 10.5" stroke="#0d0d0d" stroke-width="0.8" fill="none"/></svg>
          www.agentur-kvtl.de
        </li>
      </ul>
    </div>
  </section>
  <section class="card card--logo">
    <span class="brand-mark"></span>
    <span class="brand-name">KVTL</span>
  </section>
</main>
</body>
</html>
```